Halberd Guard Services

Our Company is a security business which needs a cut edge design, the final product should have all relevant information and maintain a bold but modern and professional look.

Target Market(s)

A cut edge design which will attract any audience

Industry/Entity Type

Security

Contact Information for Business Card

HALBERD GUARD SERVICES

Gregor Lindqvist
Operations Manager
Phone: 0491 735 219

Email: info@halberdguard.com.au
Web: www.halberdguard.com.au

Requirements
Must have
• Must be double sided and contain all relevant information and the company logo.

```html
<!DOCTYPE html>
<html lang="en">
<head>
<meta charset="utf-8">
<title>Halberd Guard Services – Business Card</title>
<link rel="stylesheet" href="https://fonts.googleapis.com/css2?family=Open+Sans:wght@400;600;800&display=swap">
<style>
  :root {
    --slate: #4e727a;
    --amber: #f2a02c;
    --ink: #1d2b31;
    --paper: #ffffff;
    --backdrop: #e6e8ea;
  }
  * { box-sizing: border-box; margin: 0; padding: 0; }
  html, body { width: 1200px; height: 951px; overflow: hidden; }
  body {
    background: var(--backdrop);
    font-family: "Open Sans", sans-serif;
    color: var(--ink);
    display: flex;
    flex-direction: column;
    align-items: center;
    justify-content: center;
    gap: 40px;
  }
  .card {
    position: relative;
    width: 760px;
    height: 434px;
    background: var(--paper);
    border-radius: 22px;
    overflow: hidden;
    box-shadow: 0 4px 14px rgba(0,0,0,0.12);
  }
  .brand {
    display: flex;
    align-items: center;
    gap: 14px;
  }
  .brand-mark {
    width: 34px;
    height: 34px;
    background: var(--slate);
    flex: none;
  }
  .brand-name {
    font-weight: 800;
    color: var(--slate);
    letter-spacing: 0.5px;
    line-height: 1.05;
  }

  /* Front */
  .card-front .brand {
    position: absolute;
    left: 90px;
    top: 170px;
  }
  .card-front .brand-mark { width: 52px; height: 52px; }
  .card-front .brand-name { font-size: 38px; }

  /* Back */
  .card-back .wave {
    position: absolute;
    inset: 0;
    width: 100%;
    height: 100%;
  }
  .card-back .brand {
    position: absolute;
    left: 60px;
    top: 52px;
  }
  .card-back .brand-name { font-size: 26px; }
  .contact {
    position: absolute;
    left: 60px;
    top: 248px;
    list-style: none;
    font-size: 19px;
    font-weight: 600;
    line-height: 1.3;
  }
  .contact li {
    display: flex;
    align-items: flex-start;
    gap: 12px;
    margin-bottom: 10px;
  }
  .contact svg { width: 18px; height: 18px; margin-top: 4px; flex: none; }
  .contact .accent { color: var(--amber); }
  .person {
    position: absolute;
    right: 40px;
    width: 250px;
    top: 318px;
    text-align: center;
    color: var(--paper);
  }
  .person-name { font-size: 25px; font-weight: 600; white-space: nowrap; }
  .person-role { font-size: 17px; font-weight: 400; white-space: nowrap; }
</style>
</head>
<body>

<section class="card card-front" aria-label="Card front">
  <div class="brand">
    <span class="brand-mark"></span>
    <span class="brand-name">HALBERD GUARD<br>SERVICES</span>
  </div>
</section>

<section class="card card-back" aria-label="Card back">
  <svg class="wave" viewBox="0 0 760 434" preserveAspectRatio="none" aria-hidden="true">
    <path d="M470 0 C420 90 500 180 460 270 C430 340 420 400 420 434 L760 434 L760 0 Z" fill="var(--amber)"/>
    <path d="M515 0 C470 90 545 180 505 270 C478 340 470 400 470 434 L760 434 L760 0 Z" fill="var(--slate)"/>
  </svg>

  <div class="brand">
    <span class="brand-mark"></span>
    <span class="brand-name">HALBERD GUARD<br>SERVICES</span>
  </div>

  <ul class="contact">
    <li>
      <svg viewBox="0 0 20 20"><path d="M5 2 L8 6 L6 8 C7 11 9 13 12 14 L14 12 L18 15 L16 18 C9 18 2 11 2 4 Z" fill="var(--amber)"/></svg>
      <span>0491 735 219</span>
    </li>
    <li>
      <svg viewBox="0 0 20 20"><rect x="2" y="5" width="16" height="11" rx="1" fill="var(--amber)"/><path d="M2 5 L10 11 L18 5" stroke="#fff" stroke-width="1.5" fill="none"/></svg>
      <span>info@halberdguard.com.au</span>
    </li>
    <li>
      <svg viewBox="0 0 20 20"><circle cx="10" cy="10" r="8" fill="var(--amber)"/></svg>
      <span>www.<span class="accent">halberdguard</span>.com.au</span>
    </li>
  </ul>

  <div class="person">
    <div class="person-name">Gregor Lindqvist</div>
    <div class="person-role">Operations Manager</div>
  </div>
</section>

</body>
</html>
```